Panty packaging

what we are looking for is 1 of a kind packaging for women's panties. It should have the same theme for all styles but a different outline or a color code setting the difference between styles. Most company's are packaging in a poly bag or hanger, what we are looking for is a box packaging. also customer should be able to see whats in the box without having to open the box. If there are different colors, the window should show that. We want to be able to customize the design for different styles and for 1 color package or multi color package. It should be sleek and sophisticated. Box does not have to be square, it can have curved edges or be totally round, the most important thins is that it should be stack-able. Sometimes the box will hold a pack of 3 and sometimes a single item, so box height may vary. We need a graphic on the box to indicate the style, for example: hipster, brief, hi cut, or lo cut. box needs a space to put a small size chart. Out logo can be color changed to match theme and background colors, just stick with the 3 colors, black, white, and magneta.
Female market all ages. upscale market
It Company

```html
<!DOCTYPE html>
<html lang="en">
<head>
<meta charset="utf-8">
<title>Velane Box Packaging</title>
<link href="https://fonts.googleapis.com/css2?family=Josefin+Sans:wght@300&family=UnifrakturMaguntia&display=swap" rel="stylesheet">
<style>
  :root {
    --page-bg: #e9e9ea;
    --black-top: #333335;
    --black-front: #161617;
    --black-edge: #0c0c0d;
    --grey-top: #acacae;
    --grey-front: #9a9a9c;
    --grey-edge: #818183;
    --white-top: #f6f6f6;
    --white-front: #e6e6e6;
    --white-edge: #cfcfcf;
    --magenta: #e0147f;
    --orange: #f39a12;
    --blue: #1e6fe0;
    --green: #7bd321;
    --outline-light: rgba(225, 225, 225, 0.7);
    --outline-dark: rgba(140, 140, 140, 0.5);
    --ink-light: #f2f2f2;
    --ink-dark: #1b1b1b;
    --depth: 58px;
    --edge: 12px;
  }
  * { box-sizing: border-box; margin: 0; padding: 0; }
  html, body { width: 1200px; height: 800px; overflow: hidden; }
  body {
    background: var(--page-bg);
    font-family: "Josefin Sans", sans-serif;
    display: flex;
    justify-content: center;
    align-items: center;
    gap: 44px;
  }
  .texture-defs { position: absolute; width: 0; height: 0; }

  .box {
    position: relative;
    width: calc(320px + var(--edge));
    height: calc(600px + var(--depth));
    filter: drop-shadow(6px 10px 10px rgba(0,0,0,0.28));
  }

  /* top face */
  .box-top {
    position: absolute; left: 0; top: 0;
    width: 320px; height: 600px;
    display: flex; flex-direction: column;
    overflow: hidden;
  }
  .grain { position: absolute; inset: 0; width: 100%; height: 100%; pointer-events: none; }

  .sleeve { position: relative; height: 330px; display: flex; flex-direction: column; align-items: center; justify-content: center; box-shadow: 0 3px 6px rgba(0,0,0,0.25); z-index: 1; }
  .style-outline { position: absolute; inset: 20px; width: calc(100% - 40px); height: calc(100% - 40px); }
  .style-outline path { fill: none; stroke-width: 9; stroke-linejoin: round; }
  .brand-name { position: relative; font-size: 40px; font-weight: 300; letter-spacing: 2px; }
  .style-name { position: relative; font-family: "UnifrakturMaguntia", serif; font-size: 15px; margin-top: 2px; margin-left: 90px; }

  .window { position: relative; height: 84px; border-top: 3px solid rgba(255,255,255,0.75); border-bottom: 3px solid rgba(255,255,255,0.75); }
  .window::after { content: ""; position: absolute; inset: 0; background: linear-gradient(180deg, rgba(255,255,255,0.35), transparent 40%, rgba(255,255,255,0.2)); }

  .cap { flex: 1; position: relative; display: flex; flex-direction: column; align-items: center; justify-content: space-between; padding: 48px 0 20px; box-shadow: 0 -3px 6px rgba(0,0,0,0.2); }
  .ring { width: 26px; height: 26px; border-radius: 50%; border: 3px solid; position: relative; }
  .size-chart { position: relative; display: flex; align-items: flex-end; gap: 12px; font-size: 13px; }
  .size-label { font-family: "UnifrakturMaguntia", serif; font-size: 15px; margin-right: 4px; line-height: 1; }
  .size-cell { display: flex; flex-direction: column; align-items: center; gap: 4px; line-height: 1; }
  .size-dot { width: 8px; height: 8px; border-radius: 50%; border: 1px solid currentColor; opacity: 0.7; }
  .size-dot.is-on { border: none; opacity: 1; }

  /* front face (box thickness) */
  .box-front {
    position: absolute; left: 0; top: 600px;
    width: 320px; height: var(--depth);
    transform-origin: top left;
    transform: skewX(11.7deg);
    overflow: hidden;
  }
  .box-front-inner {
    position: relative;
    height: 100%;
    transform-origin: top left;
    transform: skewX(-11.7deg);
    display: flex; align-items: center; justify-content: space-between;
    padding: 0 16px 0 14px;
  }
  /* right face */
  .box-edge {
    position: absolute; left: 320px; top: 0;
    width: var(--edge); height: calc(600px + var(--depth));
    clip-path: polygon(0 0, 100% var(--depth), 100% 100%, 0 calc(100% - var(--depth)));
  }

  .side-brand { position: relative; font-size: 17px; font-weight: 300; letter-spacing: 1px; }
  .legend { position: relative; display: grid; grid-template-columns: auto auto; column-gap: 14px; row-gap: 4px; }
  .legend-item { display: flex; align-items: center; gap: 5px; font-family: "UnifrakturMaguntia", serif; font-size: 12px; line-height: 1; }
  .legend-dot { width: 7px; height: 7px; border-radius: 50%; }
  .legend-icon { width: 12px; height: 11px; }

  /* Black - Hi Cut */
  .box--hicut .box-top, .box--hicut .sleeve, .box--hicut .cap { background: var(--black-top); color: var(--ink-light); }
  .box--hicut .box-front { background: var(--black-front); color: var(--ink-light); }
  .box--hicut .box-edge { background: var(--black-edge); }
  .box--hicut .grain { mix-blend-mode: overlay; opacity: 0.45; }
  .box--hicut .style-outline path { stroke: var(--outline-light); }
  .box--hicut .window { background: linear-gradient(90deg, #f4f2c8, #fffde6 50%, #eeeab6); }
  .box--hicut .ring { border-color: var(--orange); }
  .box--hicut .legend-icon { fill: #9a9a9a; }

  /* Grey - Brief */
  .box--brief .box-top, .box--brief .sleeve, .box--brief .cap { background: var(--grey-top); color: var(--ink-dark); }
  .box--brief .box-front { background: var(--grey-front); color: var(--ink-dark); }
  .box--brief .box-edge { background: var(--grey-edge); }
  .box--brief .grain { mix-blend-mode: overlay; opacity: 0.5; }
  .box--brief .style-outline path { stroke: var(--outline-light); }
  .box--brief .window { background: linear-gradient(90deg, #9c7a5a, #d8b89a 50%, #a5835f); }
  .box--brief .ring { border-color: var(--magenta); }
  .box--brief .brand-name { color: #2a2a2a; }
  .box--brief .side-brand { color: var(--magenta); }
  .box--brief .legend-icon { fill: #e2e2e2; }

  /* White - Hipster */
  .box--hipster .box-top, .box--hipster .sleeve, .box--hipster .cap { background: var(--white-top); color: var(--ink-dark); }
  .box--hipster .box-front { background: var(--white-front); color: var(--ink-dark); }
  .box--hipster .box-edge { background: var(--white-edge); }
  .box--hipster .grain { mix-blend-mode: multiply; opacity: 0.18; }
  .box--hipster .style-outline path { stroke: var(--outline-dark); }
  .box--hipster .window { background: linear-gradient(90deg, #8a1850, #c9578f 50%, #8e1b55); }
  .box--hipster .ring { border-color: var(--blue); }
  .box--hipster .brand-name, .box--hipster .side-brand { color: #1b2a55; }
  .box--hipster .legend-icon { fill: #b9b9b9; }

  .dot-magenta { background: var(--magenta); color: var(--magenta); }
  .dot-blue { background: var(--blue); color: var(--blue); }
  .dot-orange { background: var(--orange); color: var(--orange); }
  .dot-green { background: var(--green); color: var(--green); }
</style>
</head>
<body>

<svg class="texture-defs" aria-hidden="true">
  <defs>
    <filter id="leather" x="0" y="0" width="100%" height="100%">
      <feTurbulence type="fractalNoise" baseFrequency="0.11" numOctaves="3" seed="4"/>
      <feColorMatrix type="matrix" values="0 0 0 0 0.5  0 0 0 0 0.5  0 0 0 0 0.5  0 0 0 0 1"/>
      <feComponentTransfer>
        <feFuncR type="discrete" tableValues="0.15 0.4 0.6 0.85"/>
        <feFuncG type="discrete" tableValues="0.15 0.4 0.6 0.85"/>
        <feFuncB type="discrete" tableValues="0.15 0.4 0.6 0.85"/>
      </feComponentTransfer>
    </filter>
    <filter id="leather-noise" x="0" y="0" width="100%" height="100%">
      <feTurbulence type="fractalNoise" baseFrequency="0.12" numOctaves="3" seed="7" result="n"/>
      <feColorMatrix in="n" type="saturate" values="0"/>
    </filter>
  </defs>
</svg>

<!-- Hi Cut box -->
<article class="box box--hicut">
  <div class="box-top">
    <section class="sleeve">
      <svg class="grain" aria-hidden="true"><rect width="100%" height="100%" filter="url(#leather-noise)"/></svg>
      <svg class="style-outline" viewBox="0 0 280 290" preserveAspectRatio="none" aria-hidden="true">
        <path d="M20 50 L262 30 Q200 120 168 262 Q120 140 20 50 Z"/>
      </svg>
      <span class="brand-name">VELANE</span>
      <span class="style-name">Hi Cut</span>
    </section>
    <div class="window"></div>
    <section class="cap">
      <svg class="grain" aria-hidden="true"><rect width="100%" height="100%" filter="url(#leather-noise)"/></svg>
      <span class="ring"></span>
      <div class="size-chart">
        <span class="size-label">Size</span>
        <span class="size-cell"><span class="size-dot"></span>5</span>
        <span class="size-cell"><span class="size-dot is-on dot-orange"></span>6</span>
        <span class="size-cell"><span class="size-dot"></span>7</span>
        <span class="size-cell"><span class="size-dot"></span>8</span>
        <span class="size-cell"><span class="size-dot"></span>9</span>
      </div>
    </section>
  </div>
  <div class="box-edge"></div>
  <footer class="box-front">
    <div class="box-front-inner">
      <span class="side-brand">VELANE</span>
      <div class="legend">
        <span class="legend-item"><span class="legend-dot dot-magenta"></span><svg class="legend-icon" viewBox="0 0 12 11"><path d="M1 1 H11 L10 6 Q6 11 2 6 Z"/></svg>Brief</span>
        <span class="legend-item"><span class="legend-dot dot-orange"></span><svg class="legend-icon" viewBox="0 0 12 11"><path d="M0 1 L12 1 L7 10 Z"/></svg>Hi Cut</span>
        <span class="legend-item"><span class="legend-dot dot-blue"></span><svg class="legend-icon" viewBox="0 0 12 11"><path d="M1 1 H11 L10 7 Q6 9 2 7 Z"/></svg>Hipster</span>
        <span class="legend-item"><span class="legend-dot dot-green"></span><svg class="legend-icon" viewBox="0 0 12 11"><path d="M0 2 L12 2 L8 9 L4 9 Z"/></svg>Lo Cut</span>
      </div>
    </div>
  </footer>
</article>

<!-- Brief box -->
<article class="box box--brief">
  <div class="box-top">
    <section class="sleeve">
      <svg class="grain" aria-hidden="true"><rect width="100%" height="100%" filter="url(#leather-noise)"/></svg>
      <svg class="style-outline" viewBox="0 0 280 290" preserveAspectRatio="none" aria-hidden="true">
        <path d="M22 50 Q140 22 258 50 L250 150 Q205 220 160 266 Q100 222 34 160 Z"/>
      </svg>
      <span class="brand-name">VELANE</span>
      <span class="style-name">Brief</span>
    </section>
    <div class="window"></div>
    <section class="cap">
      <svg class="grain" aria-hidden="true"><rect width="100%" height="100%" filter="url(#leather-noise)"/></svg>
      <span class="ring"></span>
      <div class="size-chart">
        <span class="size-label">Size</span>
        <span class="size-cell"><span class="size-dot"></span>5</span>
        <span class="size-cell"><span class="size-dot is-on dot-magenta"></span>6</span>
        <span class="size-cell"><span class="size-dot"></span>7</span>
        <span class="size-cell"><span class="size-dot"></span>8</span>
        <span class="size-cell"><span class="size-dot"></span>9</span>
      </div>
    </section>
  </div>
  <div class="box-edge"></div>
  <footer class="box-front">
    <div class="box-front-inner">
      <span class="side-brand">VELANE</span>
      <div class="legend">
        <span class="legend-item"><span class="legend-dot dot-magenta"></span><svg class="legend-icon" viewBox="0 0 12 11"><path d="M1 1 H11 L10 6 Q6 11 2 6 Z"/></svg>Brief</span>
        <span class="legend-item"><span class="legend-dot dot-orange"></span><svg class="legend-icon" viewBox="0 0 12 11"><path d="M0 1 L12 1 L7 10 Z"/></svg>Hi Cut</span>
        <span class="legend-item"><span class="legend-dot dot-blue"></span><svg class="legend-icon" viewBox="0 0 12 11"><path d="M1 1 H11 L10 7 Q6 9 2 7 Z"/></svg>Hipster</span>
        <span class="legend-item"><span class="legend-dot dot-green"></span><svg class="legend-icon" viewBox="0 0 12 11"><path d="M0 2 L12 2 L8 9 L4 9 Z"/></svg>Lo Cut</span>
      </div>
    </div>
  </footer>
</article>

<!-- Hipster box -->
<article class="box box--hipster">
  <div class="box-top">
    <section class="sleeve">
      <svg class="grain" aria-hidden="true"><rect width="100%" height="100%" filter="url(#leather-noise)"/></svg>
      <svg class="style-outline" viewBox="0 0 280 290" preserveAspectRatio="none" aria-hidden="true">
        <path d="M18 70 Q140 44 262 70 L252 170 Q220 232 140 236 Q62 230 30 180 Z"/>
      </svg>
      <span class="brand-name">VELANE</span>
      <span class="style-name">Hipster</span>
    </section>
    <div class="window"></div>
    <section class="cap">
      <svg class="grain" aria-hidden="true"><rect width="100%" height="100%" filter="url(#leather-noise)"/></svg>
      <span class="ring"></span>
      <div class="size-chart">
        <span class="size-label">Size</span>
        <span class="size-cell"><span class="size-dot"></span>5</span>
        <span class="size-cell"><span class="size-dot is-on dot-blue"></span>6</span>
        <span class="size-cell"><span class="size-dot"></span>7</span>
        <span class="size-cell"><span class="size-dot"></span>8</span>
        <span class="size-cell"><span class="size-dot"></span>9</span>
      </div>
    </section>
  </div>
  <div class="box-edge"></div>
  <footer class="box-front">
    <div class="box-front-inner">
      <span class="side-brand">VELANE</span>
      <div class="legend">
        <span class="legend-item"><span class="legend-dot dot-magenta"></span><svg class="legend-icon" viewBox="0 0 12 11"><path d="M1 1 H11 L10 6 Q6 11 2 6 Z"/></svg>Brief</span>
        <span class="legend-item"><span class="legend-dot dot-orange"></span><svg class="legend-icon" viewBox="0 0 12 11"><path d="M0 1 L12 1 L7 10 Z"/></svg>Hi Cut</span>
        <span class="legend-item"><span class="legend-dot dot-blue"></span><svg class="legend-icon" viewBox="0 0 12 11"><path d="M1 1 H11 L10 7 Q6 9 2 7 Z"/></svg>Hipster</span>
        <span class="legend-item"><span class="legend-dot dot-green"></span><svg class="legend-icon" viewBox="0 0 12 11"><path d="M0 2 L12 2 L8 9 L4 9 Z"/></svg>Lo Cut</span>
      </div>
    </div>
  </footer>
</article>

</body>
</html>
```